Heron Loan Partners Business Card

We need a business card design for our mortgage servicing company. In addition to servicing the loans of homeowners, we help homeowners with purchasing their homes and any mortgage refinancing. We would like to see designs that use the colors in the logo attached below (gold-ish yellow and navy blue), and any other design you deem fit! The design should communicate a simpler life with smart mortgages provided by Heron.

```html
<!DOCTYPE html>
<html lang="en">
<head>
<meta charset="utf-8">
<title>Heron Loan Partners Business Card</title>
<link rel="stylesheet" href="https://fonts.googleapis.com/css2?family=Open+Sans:wght@400;600;700&display=swap">
<style>
  :root {
    --gold: #e2b43c;
    --navy: #231c5a;
    --white: #ffffff;
    --ink: #1c1c24;
    --stage: #2b2f36;
  }
  * { box-sizing: border-box; margin: 0; padding: 0; }
  html, body {
    width: 1200px; height: 780px; overflow: hidden;
    background: var(--stage);
    font-family: "Open Sans", Arial, sans-serif;
  }
  .sheet {
    width: 1200px; height: 780px;
    display: flex; align-items: center; justify-content: center; gap: 40px;
  }
  .card {
    position: relative;
    width: 540px; height: 310px;
    border-radius: 18px;
    overflow: hidden;
    box-shadow: 0 14px 30px rgba(0,0,0,.35);
  }
  .card--front { background: var(--white); }
  .card--back { background: var(--gold); display: flex; align-items: center; justify-content: center; }

  .front-wave { position: absolute; inset: 0; width: 540px; height: 310px; }

  .brand {
    position: absolute; display: flex; align-items: center; gap: 8px;
    color: var(--navy); font-weight: 700; white-space: nowrap;
  }
  .brand__dot { border-radius: 50%; background: var(--navy); flex: none; }
  .card--front .brand { left: 28px; top: 58px; font-size: 17px; }
  .card--front .brand__dot { width: 13px; height: 13px; }
  .card--back .brand { position: static; font-size: 40px; }
  .card--back .brand__dot { width: 26px; height: 26px; }

  .divider {
    position: absolute; left: 266px; top: 62px;
    width: 1px; height: 180px; background: var(--ink);
  }
  .contact {
    position: absolute; left: 286px; top: 72px;
    color: var(--ink);
  }
  .contact__name { font-size: 25px; font-weight: 700; line-height: 1.1; letter-spacing: .3px; }
  .contact__first { color: var(--gold); }
  .contact__last { color: var(--navy); }
  .contact__role { font-size: 15px; font-weight: 600; margin-top: 2px; }
  .contact__address { font-size: 14px; line-height: 1.4; margin-top: 8px; }
  .contact__list { list-style: none; font-size: 14px; line-height: 1.45; margin-top: 4px; }
  .contact__list li { display: flex; align-items: center; gap: 7px; }
  .icon { width: 12px; height: 12px; flex: none; fill: var(--navy); }
</style>
</head>
<body>
<main class="sheet">
  <section class="card card--front" aria-label="Business card front">
    <svg class="front-wave" viewBox="0 0 540 310" aria-hidden="true">
      <path d="M0,118 C20,190 90,225 190,250 C310,280 430,278 505,310 L0,310 Z" fill="var(--gold)"/>
      <path d="M8,104 C28,178 98,212 198,238 C318,268 438,268 512,306" fill="none" stroke="var(--navy)" stroke-width="4"/>
    </svg>

    <div class="brand">
      <span class="brand__dot"></span>
      <span class="brand__name">Heron Loan Partners</span>
    </div>

    <div class="divider"></div>

    <div class="contact">
      <p class="contact__name"><span class="contact__first">Lena</span> <span class="contact__last">Markovic</span></p>
      <p class="contact__role">Managing Director</p>
      <p class="contact__address">1840 Willow Bend Rd. Suite 310<br>Arlington, TX 76011</p>
      <ul class="contact__list">
        <li><svg class="icon" viewBox="0 0 12 12"><path d="M2.5 0.8 4.3 3 3.4 4.2c.6 1.6 1.8 2.8 3.4 3.4L8 6.7l2.2 1.8-.9 2.2C5 10.6 1.4 7 1.3 2z"/></svg>(555) 214-8830</li>
        <li><svg class="icon" viewBox="0 0 12 12"><path d="M1 2.5h10v7H1zM1.6 3l4.4 3.4L10.4 3" stroke="#fff" stroke-width=".9"/></svg>info@heronloan.com</li>
        <li><svg class="icon" viewBox="0 0 12 12"><circle cx="6" cy="6" r="5.5"/><path d="M.5 6h11M6 .5c-2.4 3-2.4 8 0 11M6 .5c2.4 3 2.4 8 0 11" fill="none" stroke="#fff" stroke-width=".8"/></svg>www.heronloan.com</li>
      </ul>
    </div>
  </section>

  <section class="card card--back" aria-label="Business card back">
    <div class="brand">
      <span class="brand__dot"></span>
      <span class="brand__name">Heron Loan Partners</span>
    </div>
  </section>
</main>
</body>
</html>
```